A Label for an ECO Friendly Spirit Company

Design a label which can be used for vodka and gin (London Dry Gin). It should be Square type Like the Shape File you see in the uploads. KIRO means Kind Inventive Rare and Original. We want a cool and slim label that calls for eco-friendly. We want to use it for our premium
Vodka and our London Dry Gin. Please use the logo and design it in Square Type.

40%vol, 700ml

Target Market(s)

spirits and events

Industry/Entity Type

SPIRITS

Colors
00AB8E
00BBA5
67D7C9
C6EFE9
E9F9F6
59FF00
82FF00
B8FF75
E3FFCB
F4FFEA

Requirements
Must have
• Logo from KIRO, Squaee Shape

```html
<!DOCTYPE html>
<html lang="en">
<head>
<meta charset="utf-8">
<title>KIRO Spirit Label</title>
<link href="https://fonts.googleapis.com/css2?family=Montserrat:wght@500;600;700&display=swap" rel="stylesheet">
<style>
  :root {
    --paper: #ffffff;
    --label-black: #000000;
    --teal: #00ab8e;
    --lime: #8dc63f;
  }
  html, body {
    margin: 0;
    padding: 0;
    width: 1200px;
    height: 1200px;
    overflow: hidden;
    background: var(--paper);
  }
  .label-canvas {
    display: block;
    width: 1200px;
    height: 1200px;
    font-family: "Montserrat", sans-serif;
  }
  .label-body { fill: var(--label-black); }
  .pill-rim { fill: var(--lime); }
  .pill-core { fill: var(--teal); }
  .brand-name { fill: var(--label-black); font-weight: 600; font-size: 82px; }
  .tagline-top { fill: var(--teal); font-weight: 600; font-size: 25px; }
  .tagline-bottom { fill: var(--lime); font-weight: 600; font-size: 19px; }
  .volume-abv { fill: var(--lime); font-weight: 700; font-size: 25px; }
  .volume-ml { fill: var(--teal); font-weight: 700; font-size: 25px; }
  .mark-square { fill: var(--lime); }
  .mark-name { fill: var(--teal); font-weight: 700; }
</style>
</head>
<body>
<svg class="label-canvas" viewBox="0 0 1200 1200" xmlns="http://www.w3.org/2000/svg">
  <defs>
    <clipPath id="label-shape">
      <polygon points="645,246 1014,609 645,972 277,609"/>
    </clipPath>
  </defs>

  <polygon class="label-body" points="645,246 1014,609 645,972 277,609"/>

  <g class="brand-pill" clip-path="url(#label-shape)">
    <path class="pill-rim" d="M260 536 H524 A72 72 0 0 1 524 680 H260 Z"/>
    <path class="pill-core" d="M260 544 H524 A64 64 0 0 1 524 672 H260 Z"/>
  </g>
  <text class="brand-name" x="352" y="638">KIRO</text>

  <text class="tagline-top" x="645" y="603" textLength="304" lengthAdjust="spacingAndGlyphs">KIND INVENTIVE</text>
  <text class="tagline-bottom" x="639" y="634" textLength="304" lengthAdjust="spacing">RARE AND ORIGINAL</text>

  <g class="brand-mark-top">
    <rect class="mark-square" x="586" y="416" width="34" height="34" rx="6"/>
    <text class="mark-name" x="630" y="446" font-size="34">KIRO</text>
  </g>

  <text x="520" y="776"><tspan class="volume-abv">40%VOL</tspan><tspan class="volume-ml" dx="12">700ML</tspan></text>

  <text class="mark-name brand-mark-bottom" x="635" y="894" font-size="24" text-anchor="middle">KIRO</text>
</svg>
</body>
</html>
```